Mastering Modern Vineyard Management

size of the ad - 8”x 10.75" plus 0.25" bleed
I would like an ad for a magazine that will stand out and make people want to read the ad.
The ad should not be crowded and people reading the ad will be able to read the text.
I would like it to be a creative and modern-day design.
the list of topics should not be the focus of the ad.
the text is attached.
If you decide to use people in the ad then please no ladies.
please note that leave over 1 inch for the bottom of the footer

```html
<!DOCTYPE html>
<html lang="en">
<head>
<meta charset="utf-8">
<title>Vineyard Course – Magazine Ad</title>
<link href="https://fonts.googleapis.com/css2?family=Oswald:wght@200;300;400;500;600;700&family=Montserrat:wght@700&display=swap" rel="stylesheet">
<style>
  :root{
    --ink:#000000;
    --paper:#ffffff;
    --green:#6dbb45;
    --stage:#d9d9d9;
    --photo-sky:#c9d3dc;
    --photo-grass:#6e9a4a;
    --photo-suit:#9a9ea3;
    --audience-dark:#14171a;
    --audience-mid:#2c3034;
  }
  *{margin:0;padding:0;box-sizing:border-box}
  html,body{width:1200px;height:2266px;overflow:hidden;background:var(--stage)}
  .ad{
    position:absolute;left:50px;top:405px;
    width:612px;height:810px;
    transform:scale(1.7974);transform-origin:0 0;
    background:var(--paper);overflow:hidden;
    font-family:'Oswald',sans-serif;color:var(--paper);
    box-shadow:0 6px 14px rgba(0,0,0,.35);
  }
  .ad-shapes{position:absolute;inset:0}
  .t{position:absolute;text-transform:uppercase;line-height:1;white-space:nowrap}
  .kicker{left:36px;top:76px;font-size:40px;font-weight:200;letter-spacing:-.5px}
  .title{left:34px;top:108px;font-size:84px;font-weight:600;letter-spacing:-1px;line-height:.95}
  .title .accent{color:var(--green)}
  .course-name{left:36px;top:203px;font-size:21px;font-weight:400;color:var(--ink);line-height:1.1}
  .tagline{left:36px;top:271px;font-size:14px;font-weight:300}
  .location{left:36px;top:307px;font-size:30px;font-weight:600;color:var(--ink)}
  .details{left:36px;top:345px;font-size:12px;font-weight:400;color:var(--ink);line-height:20px;letter-spacing:-.2px}
  .offer{left:36px;top:428px;font-size:17px;font-weight:500;color:var(--green)}
  .offer-note{left:36px;top:453px;font-size:12px;font-weight:300}
  .topics-head{left:36px;top:487px;font-size:30px;font-weight:500}
  .topics-head .accent{color:var(--green)}
  .topics{position:absolute;top:535px;list-style:none;font-size:12px;font-weight:300;text-transform:uppercase;line-height:20px}
  .topics.col-a{left:36px}
  .topics.col-b{left:276px}
  .topics li{display:flex;align-items:center;gap:10px;white-space:nowrap}
  .topics svg{width:9px;height:9px;flex:none}
  .footer-note{position:absolute;left:0;right:0;top:742px;text-align:center;font-family:'Montserrat',sans-serif;font-weight:700;font-size:10px}
  .footer-note svg{display:block;margin:0 auto;width:10px;height:14px}
  .footer-note span{display:block;margin:4px 0}
</style>
</head>
<body>
<div class="ad">
  <svg class="ad-shapes" viewBox="0 0 612 810" width="612" height="810">
    <defs>
      <linearGradient id="skyline" x1="0" y1="0" x2="0" y2="1">
        <stop offset="0" stop-color="var(--photo-sky)"/>
        <stop offset=".55" stop-color="var(--photo-suit)"/>
        <stop offset="1" stop-color="var(--photo-grass)"/>
      </linearGradient>
      <linearGradient id="street" x1="0" y1="0" x2="1" y2="1">
        <stop offset="0" stop-color="#dfe6ec"/>
        <stop offset="1" stop-color="#9fa9b2"/>
      </linearGradient>
      <linearGradient id="audience" x1="0" y1="0" x2="1" y2="0">
        <stop offset="0" stop-color="var(--audience-dark)"/>
        <stop offset=".5" stop-color="var(--audience-mid)"/>
        <stop offset="1" stop-color="var(--audience-dark)"/>
      </linearGradient>
    </defs>
    <rect class="header-band" x="0" y="0" width="612" height="195" fill="var(--ink)"/>
    <path class="name-band" d="M0 195 H300 L325 251 H0 Z" fill="var(--paper)"/>
    <rect class="tagline-band" x="0" y="251" width="612" height="50" fill="var(--ink)"/>
    <path class="topics-band" d="M0 410 H470 C560 410 605 380 612 310 V660 H0 Z" fill="var(--ink)"/>
    <rect role="img" aria-label="Dim photo of a seminar audience" x="0" y="410" width="612" height="250" fill="url(#audience)" opacity=".9"/>
    <path d="M470 410 C560 410 605 380 612 310 V410 Z" fill="var(--ink)"/>
    <rect class="footer-band" x="0" y="720" width="612" height="90" fill="var(--ink)"/>
    <circle cx="488" cy="160" r="172" fill="var(--paper)"/>
    <circle cx="478" cy="162" r="150" fill="var(--green)"/>
    <circle role="img" aria-label="Photo of a smiling instructor giving a thumbs up before a landscape" cx="492" cy="160" r="144" fill="url(#skyline)"/>
    <circle cx="548" cy="578" r="134" fill="var(--ink)"/>
    <circle cx="540" cy="580" r="127" fill="var(--green)"/>
    <circle role="img" aria-label="Photo of two men talking outdoors" cx="553" cy="576" r="121" fill="url(#street)"/>
  </svg>

  <div class="t kicker">Vineyard</div>
  <div class="t title">Cour<span class="accent">s</span>e</div>
  <div class="t course-name">Mastering Modern Vineyard<br>Management</div>
  <div class="t tagline">Investing in knowledge is investing in opportunities.</div>
  <div class="t location">Harlow Glen</div>
  <div class="t details">10 -Tuesday evenings sessions<br>Starting Feb.28<br>Limited partial scholarships</div>
  <div class="t offer">Early Bird Special</div>
  <div class="t offer-note">For those that started or would like to go into viticulture</div>
  <div class="t topics-head"><span class="accent">Topics:</span> Partial Listing</div>

  <ul class="topics col-a">
    <li><svg viewBox="0 0 10 10"><circle cx="5" cy="5" r="4.5" fill="#fff"/><path d="M5 5V0.5A4.5 4.5 0 0 1 9.5 5Z" fill="#000"/></svg>Vineyard planning strategies</li>
    <li><svg viewBox="0 0 10 10"><circle cx="5" cy="5" r="4.5" fill="#fff"/><path d="M5 5V0.5A4.5 4.5 0 0 1 9.5 5Z" fill="#000"/></svg>Soil testing</li>
    <li><svg viewBox="0 0 10 10"><circle cx="5" cy="5" r="4.5" fill="#fff"/><path d="M5 5V0.5A4.5 4.5 0 0 1 9.5 5Z" fill="#000"/></svg>Irrigation</li>
    <li><svg viewBox="0 0 10 10"><circle cx="5" cy="5" r="4.5" fill="#fff"/><path d="M5 5V0.5A4.5 4.5 0 0 1 9.5 5Z" fill="#000"/></svg>Pruning</li>
    <li><svg viewBox="0 0 10 10"><circle cx="5" cy="5" r="4.5" fill="#fff"/><path d="M5 5V0.5A4.5 4.5 0 0 1 9.5 5Z" fill="#000"/></svg>Canopy management</li>
  </ul>
  <ul class="topics col-b">
    <li><svg viewBox="0 0 10 10"><circle cx="5" cy="5" r="4.5" fill="#fff"/><path d="M5 5V0.5A4.5 4.5 0 0 1 9.5 5Z" fill="#000"/></svg>Vineyard legal basics</li>
    <li><svg viewBox="0 0 10 10"><circle cx="5" cy="5" r="4.5" fill="#fff"/><path d="M5 5V0.5A4.5 4.5 0 0 1 9.5 5Z" fill="#000"/></svg>Sourcing vines</li>
    <li><svg viewBox="0 0 10 10"><circle cx="5" cy="5" r="4.5" fill="#fff"/><path d="M5 5V0.5A4.5 4.5 0 0 1 9.5 5Z" fill="#000"/></svg>Pest control</li>
    <li><svg viewBox="0 0 10 10"><circle cx="5" cy="5" r="4.5" fill="#fff"/><path d="M5 5V0.5A4.5 4.5 0 0 1 9.5 5Z" fill="#000"/></svg>Dealing with buyers</li>
    <li><svg viewBox="0 0 10 10"><circle cx="5" cy="5" r="4.5" fill="#fff"/><path d="M5 5V0.5A4.5 4.5 0 0 1 9.5 5Z" fill="#000"/></svg>Harvest fundamentals</li>
  </ul>

  <div class="footer-note">
    <svg viewBox="0 0 10 14" aria-hidden="true"><path d="M5 0 L10 6 H6.5 V14 H3.5 V6 H0 Z" fill="#fff"/></svg>
    <span>1 inch Free</span>
    <svg viewBox="0 0 10 14" aria-hidden="true"><path d="M5 14 L10 8 H6.5 V0 H3.5 V8 H0 Z" fill="#fff"/></svg>
  </div>
</div>
</body>
</html>
```